Website for software company "velora"

We need a website for our software company/startup named "velora". We are developing several products (currently 3 standard-software products) which are all in different sectors, but all our products are available for Laptops/PC/Mobile Phones/Tablets, ... We do also create custom software and support our customers with consulting to optimize their processes.
We already have a Logo which you can find in the attached files.
We are a young team of 4 members (two founders and 2 employees).

To get an idea of our products -> the first one is a planning software for healthcare organizations (eg. BlueHaven, firebrigade, pharmacy), the second one is a booking software for sport clubs and the third one is a competition software for sports hunting. You see very diverse. Include or ignore this info of our products as you like.

The design has to be a bootstrap 4 (or higher) design. We have licenced FontAwesome as iconset. Responsive design should come without saying.

• Starting page, product pages, news section, contact, team, services

```html
<!DOCTYPE html>
<html lang="en">
<head>
<meta charset="utf-8">
<title>velora — Software for every sector</title>
<link href="https://fonts.googleapis.com/css2?family=Montserrat:wght@400;600;700;800&family=Open+Sans:wght@400;600&display=swap" rel="stylesheet">
<style>
:root{
  --orange:#f26522;
  --orange-dark:#d9531a;
  --ink:#1f1f1f;
  --text:#555;
  --muted:#8a8a8a;
  --light:#f3f3f3;
  --white:#fff;
  --black:#0d0d0d;
}
*{box-sizing:border-box;margin:0;padding:0}
html,body{width:1200px;height:4620px;overflow:hidden}
body{font-family:"Open Sans",Arial,sans-serif;color:var(--text);background:var(--white);font-size:14px;line-height:1.6}
h1,h2,h3,h4,.brand,.btn,.nav a{font-family:Montserrat,Arial,sans-serif}
.section-title{font-size:34px;font-weight:700;color:var(--ink);text-align:center;text-transform:uppercase;letter-spacing:.5px}
.section-title::after{content:"";display:block;width:60px;height:4px;background:var(--orange);margin:14px auto 0}
.btn{display:inline-flex;align-items:center;gap:10px;background:var(--orange);color:var(--white);font-weight:700;font-size:14px;text-transform:uppercase;padding:0 22px;height:50px;letter-spacing:.5px}
.btn svg{width:14px;height:14px}

/* Hero */
.hero{position:relative;height:712px;background:linear-gradient(110deg,#3b4550 0%,#6b7480 35%,#a9a49c 60%,#7b6f66 100%);color:var(--white)}
.hero-photo{position:absolute;inset:0;background:linear-gradient(90deg,rgba(20,24,30,.55),rgba(20,24,30,.05) 70%)}
.topbar{position:absolute;top:0;left:0;right:0;height:72px;display:flex;align-items:center;padding:0 120px}
.brand{display:flex;align-items:center;gap:10px;font-size:40px;font-weight:800;color:var(--white);letter-spacing:1px}
.brand .mark{width:16px;height:16px;background:var(--orange)}
.topbar .social{display:flex;gap:10px;margin-left:auto;margin-right:40px}
.social span{width:28px;height:28px;border-radius:50%;background:var(--orange);display:block}
.contact-top{display:flex;gap:30px;font-size:15px;font-weight:600}
.contact-top div{display:flex;align-items:center;gap:8px}
.contact-top .ic{width:26px;height:26px;background:var(--white);display:flex;align-items:center;justify-content:center}
.contact-top svg{width:14px;height:14px}
.nav{position:absolute;top:72px;left:330px;width:560px;height:40px;background:var(--orange);display:flex;justify-content:center;align-items:center;gap:30px}
.nav a{color:var(--white);font-size:13px;font-weight:600;text-transform:uppercase;text-decoration:none}
.hero-copy{position:absolute;left:130px;top:230px;width:560px}
.hero-copy h1 .small{display:block;font-size:30px;font-weight:700;letter-spacing:1px}
.hero-copy h1 .big{display:block;font-size:110px;line-height:1;font-weight:800;color:var(--white);letter-spacing:2px}
.hero-copy p{font-size:15px;margin:20px 0 36px;width:500px}
.slider-arrows{position:absolute;right:0;bottom:0;display:flex}
.slider-arrows span{width:60px;height:50px;display:flex;align-items:center;justify-content:center;background:var(--white)}
.slider-arrows span+span{background:var(--orange)}
.slider-arrows svg{width:16px;height:16px}

/* Welcome */
.welcome{height:668px;background:var(--light);position:relative}
.welcome .img-a{position:absolute;left:120px;top:72px;width:250px;height:500px;background:linear-gradient(160deg,#cfd5db,#7f8a95 60%,#47505a)}
.welcome .img-b{position:absolute;left:380px;top:110px;width:260px;height:460px;background:linear-gradient(160deg,#e9e6e1,#c7bfb4 50%,#8e867b);box-shadow:0 10px 30px rgba(0,0,0,.15)}
.welcome .copy{position:absolute;left:690px;top:110px;width:400px}
.welcome h2{font-size:34px;font-weight:700;color:var(--ink);text-transform:uppercase}
.welcome h2::after{content:"";display:block;width:60px;height:4px;background:var(--orange);margin:12px 0 22px}
.welcome p{font-size:14px;text-align:justify;margin-bottom:30px}

/* Products */
.products{height:620px;padding-top:110px}
.product-row{display:flex;width:936px;margin:50px auto 0}
.product{width:312px;height:380px;position:relative;overflow:hidden}
.product .photo{position:absolute;inset:0}
.product .band{position:absolute;left:0;right:0;bottom:0;height:130px;background:#1c1c1c;color:var(--white);text-align:center;padding-top:44px}
.product.featured .band{height:200px;background:rgba(242,101,34,.88);padding-top:100px}
.product h3{font-size:17px;font-weight:700;text-transform:uppercase;line-height:1.2}
.product .more{font-family:Montserrat,sans-serif;font-size:11px;font-weight:700;text-transform:uppercase;margin-top:14px;display:block}

/* Testimonials */
.testimonials{height:520px;background:linear-gradient(120deg,var(--orange),#e8743a 50%,var(--orange-dark));padding-top:90px;position:relative}
.testimonials .section-title{color:var(--white)}
.testimonials .section-title::after{background:var(--white)}
.quotes{display:flex;gap:32px;width:936px;margin:40px auto 0}
.quote{flex:1;background:var(--white);height:240px;padding:30px 28px;display:flex;gap:24px;box-shadow:0 10px 24px rgba(0,0,0,.15)}
.quote .avatar{width:80px;height:80px;border-radius:50%;background:linear-gradient(135deg,#c9b7a7,#7a6a5e);flex:none}
.quote .qmark{font-family:Montserrat,sans-serif;font-size:60px;line-height:1;color:#ddd;margin-top:20px;text-align:center}
.quote h4{font-size:16px;font-weight:700;color:var(--ink)}
.quote .role{color:var(--orange);font-size:12px;margin-bottom:10px}
.quote p{font-size:13px}
.dots{display:flex;justify-content:center;gap:8px;margin-top:44px}
.dots span{width:9px;height:9px;border-radius:50%;background:rgba(255,255,255,.5)}
.dots span:first-child{background:var(--white)}

/* Feature */
.feature{height:640px;padding-top:110px;text-align:center}
.feature .section-title{font-size:36px}
.feature .section-title::after{display:none}
.feature p{width:940px;margin:18px auto 24px;font-size:14px}
.feature .photo{height:320px;margin-top:24px;background:linear-gradient(180deg,#f5f5f5,#c9c6c1 35%,#8b857d 70%,#5d5852)}

/* Blog */
.blog{height:620px;padding-top:80px;background:var(--light)}
.posts{display:flex;gap:32px;width:936px;margin:50px auto 0}
.post{flex:1;background:var(--white);height:360px;box-shadow:0 6px 18px rgba(0,0,0,.08);text-align:center}
.post .photo{height:180px}
.post .date{display:inline-block;background:var(--orange);color:var(--white);font-size:11px;font-weight:600;padding:3px 12px;margin-top:-12px;position:relative}
.post h3{font-size:15px;font-weight:700;color:var(--ink);text-transform:uppercase;line-height:1.3;margin:12px 20px 10px}
.post p{font-size:12px;margin:0 22px}

/* Contact */
.contact{height:500px;display:flex}
.contact .touch{width:600px;background:linear-gradient(135deg,#fafafa,#e4e4e4);padding:70px 70px 0 96px}
.contact .info{width:600px;background:linear-gradient(135deg,#e86a2c,var(--orange) 40%,#b7501f);color:var(--white);padding:70px 0 0 170px}
.contact h2{font-size:30px;font-weight:700;text-transform:uppercase;color:var(--ink)}
.contact .info h2{color:var(--white)}
.contact h2::after{content:"";display:block;width:50px;height:4px;background:var(--orange);margin:10px 0 30px}
.contact .info h2::after{background:var(--white)}
.form{display:grid;grid-template-columns:1fr 1fr;gap:12px;width:440px}
.form span{background:var(--white);border:1px solid #ddd;height:40px;font-size:12px;color:var(--muted);padding:10px 14px}
.form .msg{grid-column:1/3;height:90px}
.contact .btn{margin-top:24px;height:44px}
.info-line{display:flex;align-items:center;gap:18px;margin-bottom:24px;font-size:14px}
.info-line svg{width:22px;height:22px;flex:none}
.info .social{display:flex;gap:12px;margin-top:8px}
.info .social span{width:36px;height:36px;background:var(--white)}

/* Footer */
.footer{height:340px;background:var(--black);color:#ccc;text-align:center;padding-top:55px}
.footer .brand{justify-content:center;font-size:48px}
.footer .rule{width:960px;height:1px;background:#333;margin:26px auto}
.footer .links{display:flex;justify-content:center;gap:34px;font-family:Montserrat,sans-serif;font-size:13px;font-weight:600;color:var(--white);text-transform:uppercase}
.footer .addr{display:flex;justify-content:center;gap:60px;font-size:12px}
.footer .copy{font-size:12px;margin-top:22px;color:#999}
</style>
</head>
<body>

<header class="hero">
  <div class="hero-photo" role="img" aria-label="Photo of a team working together at computers"></div>
  <div class="topbar">
    <div class="brand"><span class="mark"></span>VELORA</div>
    <div class="social"><span></span><span></span><span></span><span></span></div>
    <div class="contact-top">
      <div><span class="ic"><svg viewBox="0 0 16 16"><rect x="1" y="3" width="14" height="10" fill="none" stroke="#f26522" stroke-width="1.6"/><path d="M1 3l7 6 7-6" fill="none" stroke="#f26522" stroke-width="1.6"/></svg></span>hello@velora-mail.com</div>
      <div><span class="ic"><svg viewBox="0 0 16 16"><path d="M3 1h3l1 4-2 1c1 2 2 3 4 4l1-2 4 1v3c0 1-1 2-2 2C7 14 2 9 1 3c0-1 1-2 2-2z" fill="#f26522"/></svg></span>+1 555 0142 300</div>
    </div>
  </div>
  <nav class="nav">
    <a>Home</a><a>About</a><a>Our Software</a><a>Testimonials</a><a>Blog</a><a>Contact</a>
  </nav>
  <div class="hero-copy">
    <h1><span class="small">WELCOME TO</span><span class="big">VELORA</span></h1>
    <p>Planning, booking and competition software built for every screen — from laptop to phone — plus custom builds and process consulting.</p>
    <a class="btn">Get Started <svg viewBox="0 0 16 16"><path d="M4 2l8 6-8 6z" fill="#fff"/></svg></a>
  </div>
  <div class="slider-arrows">
    <span><svg viewBox="0 0 16 16"><path d="M11 2L4 8l7 6z" fill="#222"/></svg></span>
    <span><svg viewBox="0 0 16 16"><path d="M5 2l7 6-7 6z" fill="#fff"/></svg></span>
  </div>
</header>

<section class="welcome">
  <div class="img-a" role="img" aria-label="Photo of a developer at a desk with monitors"></div>
  <div class="img-b" role="img" aria-label="Photo of a team member holding a tablet"></div>
  <div class="copy">
    <h2>Welcome to Velora</h2>
    <p>We are a young team of four building software that fits the way people really work. Our three products serve very different sectors, yet share one promise: they run smoothly on laptops, desktops, tablets and phones. Alongside our products we create custom software and help our customers streamline their processes through hands-on consulting. We listen first, then design tools that save time every day, and we stay close as your needs grow. Whether you plan shifts, book courts or run a competition, our goal is the same — clear, reliable software that your whole team enjoys using from the very first login.</p>
    <a class="btn">Learn More <svg viewBox="0 0 16 16"><path d="M4 2l8 6-8 6z" fill="#fff"/></svg></a>
  </div>
</section>

<section class="products">
  <h2 class="section-title">Our Software Products</h2>
  <div class="product-row">
    <div class="product">
      <div class="photo" role="img" aria-label="Photo of healthcare staff at work" style="background:linear-gradient(160deg,#c9dbe8,#7fa3bf 60%,#4d6d87)"></div>
      <div class="band"><h3>Healthcare<br>Organizations</h3><span class="more">Learn More</span></div>
    </div>
    <div class="product featured">
      <div class="photo" role="img" aria-label="Photo of a young athlete at a sports club" style="background:linear-gradient(160deg,#9bb7d6,#5c7fa5 60%,#2f4663)"></div>
      <div class="band"><h3>Sport Clubs</h3><span class="more">Learn More</span></div>
    </div>
    <div class="product">
      <div class="photo" role="img" aria-label="Photo of a sport shooter aiming outdoors" style="background:linear-gradient(160deg,#c7b58f,#8c7a56 60%,#4f4430)"></div>
      <div class="band"><h3>Sports<br>Hunting</h3><span class="more">Learn More</span></div>
    </div>
  </div>
</section>

<section class="testimonials">
  <h2 class="section-title">Our Client Testimonials</h2>
  <div class="quotes">
    <div class="quote">
      <div><div class="avatar" role="img" aria-label="Client portrait"></div><div class="qmark">“</div></div>
      <div><h4>JOHN DEO</h4><div class="role">Operations lead, clinic group</div><p>Velora replaced three spreadsheets and a whiteboard. Shift planning that took a full afternoon now takes minutes, and the team checks their schedule right on their phones.</p></div>
    </div>
    <div class="quote">
      <div><div class="avatar" role="img" aria-label="Client portrait"></div><div class="qmark">“</div></div>
      <div><h4>JOHN DEO</h4><div class="role">Board member, tennis club</div><p>Our members book courts themselves now and double bookings are gone. The support team answered every question quickly and helped us set everything up in a week.</p></div>
    </div>
  </div>
  <div class="dots"><span></span><span></span><span></span></div>
</section>

<section class="feature">
  <h2 class="section-title">Lorem Ipsum Dolor Sit Amet</h2>
  <p>Beyond our products, we build custom software and guide teams through process consulting. We map how work flows today, find where time is lost, and deliver tools that fit — tested on every device your people use, and supported long after launch.</p>
  <a class="btn">Learn More <svg viewBox="0 0 16 16"><path d="M4 2l8 6-8 6z" fill="#fff"/></svg></a>
  <div class="photo" role="img" aria-label="Photo of a business meeting around a conference table"></div>
</section>

<section class="blog">
  <h2 class="section-title">Our Latest Blog</h2>
  <div class="posts">
    <article class="post">
      <div class="photo" role="img" aria-label="Photo of a workspace with monitors" style="background:linear-gradient(160deg,#cdd3d9,#8995a1)"></div>
      <span class="date">14 APRIL 2022</span>
      <h3>Lorem ipsum dolor sit am consectetur adipiscing</h3>
      <p>Tips for moving your team schedule from paper to a shared app without losing a single shift.</p>
    </article>
    <article class="post">
      <div class="photo" role="img" aria-label="Photo of colleagues smiling at a laptop" style="background:linear-gradient(160deg,#e2d6c8,#a89078)"></div>
      <span class="date">14 APRIL 2022</span>
      <h3>Lorem ipsum dolor sit am consectetur adipiscing</h3>
      <p>How small clubs cut admin time in half by letting members book and pay on their own.</p>
    </article>
    <article class="post">
      <div class="photo" role="img" aria-label="Photo of a developer working at night" style="background:linear-gradient(160deg,#b9c2cc,#5d6773)"></div>
      <span class="date">14 APRIL 2022</span>
      <h3>Lorem ipsum dolor sit am consectetur adipiscing</h3>
      <p>What we learned building one product that feels right on a phone, a tablet and a desktop.</p>
    </article>
  </div>
</section>

<section class="contact">
  <div class="touch">
    <h2>Get in Touch</h2>
    <div class="form">
      <span>Full Name</span><span>Last Name</span>
      <span>Email</span><span>Phone</span>
      <span class="msg">Message</span>
    </div>
    <a class="btn">Submit <svg viewBox="0 0 16 16"><path d="M4 2l8 6-8 6z" fill="#fff"/></svg></a>
  </div>
  <div class="info">
    <h2>Contact Info</h2>
    <div class="info-line"><svg viewBox="0 0 24 24"><path d="M12 2a7 7 0 017 7c0 5-7 13-7 13S5 14 5 9a7 7 0 017-7zm0 4a3 3 0 100 6 3 3 0 000-6z" fill="#fff"/></svg>48 Harbor Lane, Suite 210,<br>Eastbridge</div>
    <div class="info-line"><svg viewBox="0 0 24 24"><path d="M5 2h4l2 5-3 2c1 3 3 5 6 6l2-3 5 2v4c0 2-1 3-3 3C10 21 3 14 2 5c0-2 1-3 3-3z" fill="#fff"/></svg>+1 555 0142 300</div>
    <div class="info-line"><svg viewBox="0 0 24 24"><rect x="2" y="5" width="20" height="14" fill="none" stroke="#fff" stroke-width="2"/><path d="M2 5l10 8 10-8" fill="none" stroke="#fff" stroke-width="2"/></svg>hello@velora-mail.com</div>
    <div class="social"><span style="border-radius:50%"></span><span style="border-radius:50%"></span><span style="border-radius:50%"></span><span style="border-radius:50%"></span></div>
  </div>
</section>

<footer class="footer">
  <div class="brand"><span class="mark"></span>VELORA</div>
  <div class="rule"></div>
  <div class="links"><span>Home</span><span>About</span><span>Our Software</span><span>Testimonials</span><span>Blog</span><span>Contact</span></div>
  <div class="rule"></div>
  <div class="addr"><span>+1 555 0142 300</span><span>48 Harbor Lane, Suite 210, Eastbridge</span></div>
  <div class="copy">© 2022 VELORA | All Rights Reserved.</div>
</footer>

</body>
</html>
```